Website for "Bright Morrow Ltd" cleaning bsuiness

We require a website to expose our business to the local market. We want to provide background on who we are and what we do but in an easily digestible way. We clean domestic and commercial premises and want to provide a list of all of our services to potential customers. We operate out of Warrington in the UK.

We would like the website to be animated in some way so that the experience of using it is not dull or mundane. This website needs to be an extension of our company.

Target Market(s)

30 - 60 year olds for Domestic plus commercial clients

Industry/Entity Type

Cleaning Service

Coding

Coded - Design and coding required

Number of Pages Required

4 page

Font styles to use
Sans Serif

Colors
0455a3
3176b5
85acd3
cfdeed
ffffff
000000
1b1b1b
c8c8c8
757575

Requirements
Must have
• Logo which has been provided. Theme based around the logo and its colours. Simple layout to avoid confusion.
Nice to have
• Animations where possible to impress the customer.
Should not have
• any pictures of cleaning equipment, fairies, maids etc

```html
<!DOCTYPE html>
<html lang="en">
<head>
<meta charset="utf-8">
<title>Bright Morrow Ltd – Professional Cleaning Service</title>
<link href="https://fonts.googleapis.com/css2?family=Raleway:wght@300;400;600&family=Arimo:wght@400;700&display=swap" rel="stylesheet">
<style>
:root{
  --blue-deep:#0455a3;
  --blue-mid:#3176b5;
  --blue-soft:#85acd3;
  --blue-pale:#cfdeed;
  --white:#ffffff;
  --ink:#1b1b1b;
  --rule:#c8c8c8;
  --muted:#757575;
}
*{margin:0;padding:0;box-sizing:border-box}
html,body{width:747px;height:1200px;overflow:hidden;background:var(--white)}
body{position:relative;font-family:"Arimo",Arial,sans-serif;color:var(--ink)}
.abs{position:absolute}

/* hero */
.hero-photo{left:0;top:0;width:747px;height:430px;
  background:linear-gradient(100deg,#e9edf1 0%,#f7f8fa 35%,#dfe6ec 70%,#cbd6df 100%)}
.site-nav{left:0;top:0;width:747px;height:48px}
.site-nav .rule{position:absolute;left:200px;right:0;top:48px;height:1px;background:#b9c0c7}
.site-nav a{position:absolute;top:19px;font-size:11.2px;color:#2b2f33;text-decoration:none;letter-spacing:.2px}
.site-nav a.active{color:var(--blue-deep)}
.site-nav .active-bar{position:absolute;left:210px;top:46px;width:48px;height:2px;background:var(--blue-deep)}
.brand-hero{left:0;width:747px;top:150px;text-align:center;font-family:"Raleway",sans-serif;font-weight:600;font-size:46px;color:var(--blue-deep);line-height:1.05}
.brand-hero small{display:block;font-size:18px;margin-top:10px;letter-spacing:1px}
.hero-edge{left:0;top:350px}

/* blog */
.section-title{left:0;width:747px;top:440px;text-align:center;font-family:"Raleway",sans-serif;font-weight:400;font-size:26px;color:var(--ink);letter-spacing:.5px}
.section-title span{color:var(--blue-deep)}
.post{left:48px;width:640px;height:100px}
.post-thumb{position:absolute;left:0;top:0;width:162px;height:100px;border:1px solid #ddd}
.post-body{position:absolute;left:176px;top:0;width:470px}
.post-title{font-family:"Raleway",sans-serif;font-size:13.6px;color:var(--blue-deep);font-weight:400;white-space:nowrap}
.post-date{margin-top:5px;font-size:9px;color:var(--muted);display:flex;align-items:center;gap:5px}
.post-text{margin-top:6px;font-size:8.8px;line-height:16px;color:var(--muted)}
.read-more{display:inline-flex;align-items:center;gap:3px;margin-top:3px;font-size:9.4px;font-weight:700;color:var(--blue-deep);text-decoration:none}

.pager{left:48px;top:864px;display:flex;height:22px;border:1px solid var(--rule);border-radius:2px;overflow:hidden}
.pager a{display:flex;align-items:center;justify-content:center;min-width:25px;padding:0 8px;font-size:9.6px;color:var(--ink);text-decoration:none;border-left:1px solid var(--rule)}
.pager a:first-child{border-left:0}
.pager a.current{background:var(--blue-deep);color:var(--white)}

/* footer */
.footer-photo{left:0;top:940px;width:747px;height:224px;
  background:linear-gradient(90deg,#f3efeb 0%,#f7f3f0 30%,#faf8f6 60%,#f4f2f0 100%)}
.footer-edge{left:0;top:940px}
.brand-foot{left:54px;top:1040px;width:140px;font-family:"Raleway",sans-serif;font-weight:600;font-size:20px;line-height:1.15;color:var(--blue-deep)}
.foot-col h3{font-size:11.2px;font-weight:700;color:var(--blue-deep);letter-spacing:.2px}
.links{left:219px;top:1017px}
.links ul{list-style:none;margin-top:12px}
.links li{display:flex;align-items:center;gap:8px;font-size:8.8px;color:#444;height:17px}
.links li i{width:5px;height:5px;border:1px solid var(--blue-deep);display:block}
.links li i.on{background:var(--blue-deep)}
.contact{left:378px;top:1017px;width:150px}
.contact .row{display:flex;gap:10px;font-size:8.8px;line-height:17px;color:#444}
.contact .row svg{flex:none;margin-top:2px}
.news{left:545px;top:1017px;width:160px}
.news p{margin-top:11px;font-size:8.6px;line-height:14.5px;color:#444}
.news .email{display:block;margin-top:6px;width:154px;height:25px;border:1px solid var(--rule);background:var(--white);font-size:8.8px;color:#444;padding:0 7px;line-height:23px}
.news .submit{display:block;margin-top:7px;width:96px;height:25px;background:var(--blue-deep);color:var(--white);font-size:11.2px;text-align:center;line-height:25px}
.copyright{left:0;top:1164px;width:747px;height:36px;background:var(--blue-deep);color:var(--blue-pale);font-size:8.8px;text-align:center;line-height:36px}
.copyright b{color:var(--white);font-weight:700}
</style>
</head>
<body>

<div class="abs hero-photo" role="img" aria-label="Bright, clean white living room and glass-walled office interior"></div>

<nav class="abs site-nav">
  <div class="rule"></div>
  <a href="#" class="active" style="left:218px">HOME</a>
  <a href="#" style="left:293px">ABOUT US</a>
  <a href="#" style="left:377px">SERVICES</a>
  <a href="#" style="left:459px">BLOG</a>
  <a href="#" style="left:517px">CONTACT US</a>
  <div class="active-bar"></div>
</nav>

<div class="abs brand-hero">Bright Morrow Ltd<small>Professional Cleaning Service</small></div>

<svg class="abs hero-edge" width="747" height="90" viewBox="0 0 747 90">
  <defs>
    <linearGradient id="edgeFade" x1="0" x2="1">
      <stop offset="0" stop-color="#0455a3"/><stop offset=".6" stop-color="#0455a3"/><stop offset="1" stop-color="#85acd3"/>
    </linearGradient>
  </defs>
  <polygon points="0,74 374,6 747,74 747,90 0,90" fill="#ffffff"/>
  <polyline points="0,74 374,6 747,74" fill="none" stroke="url(#edgeFade)" stroke-width="5"/>
</svg>

<h2 class="abs section-title">LATEST <span>BLOG</span></h2>

<article class="abs post" style="top:493px">
  <div class="post-thumb" role="img" aria-label="Window being wiped clean with a cloth" style="background:linear-gradient(90deg,#e8e1da,#c9d3dc)"></div>
  <div class="post-body">
    <h4 class="post-title">Lorem Ipsum is simply dummy text of the printing and typesetting industry.</h4>
    <div class="post-date"><svg width="9" height="9" viewBox="0 0 9 9"><rect x=".5" y="1.5" width="8" height="7" fill="none" stroke="#999"/><line x1=".5" y1="3.5" x2="8.5" y2="3.5" stroke="#999"/></svg>07 November 2016</div>
    <p class="post-text">Lorem Ipsum is simply dummy text of the printing and typesetting industry. Lorem Ipsum has been the industry's standard dummy text ever since the.</p>
    <a class="read-more" href="#">READ MORE <svg width="9" height="8" viewBox="0 0 9 8"><path d="M1 1l3 3-3 3M5 1l3 3-3 3" fill="none" stroke="#0455a3" stroke-width="1.4"/></svg></a>
  </div>
</article>

<article class="abs post" style="top:612px">
  <div class="post-thumb" role="img" aria-label="Team tidying a bright office corridor" style="background:linear-gradient(90deg,#eef0f2,#d5dde5)"></div>
  <div class="post-body">
    <h4 class="post-title">Lorem Ipsum is simply dummy text of the printing and typesetting industry.</h4>
    <div class="post-date"><svg width="9" height="9" viewBox="0 0 9 9"><rect x=".5" y="1.5" width="8" height="7" fill="none" stroke="#999"/><line x1=".5" y1="3.5" x2="8.5" y2="3.5" stroke="#999"/></svg>07 November 2016</div>
    <p class="post-text">Lorem Ipsum is simply dummy text of the printing and typesetting industry. Lorem Ipsum has been the industry's standard dummy text ever since the.</p>
    <a class="read-more" href="#">READ MORE <svg width="9" height="8" viewBox="0 0 9 8"><path d="M1 1l3 3-3 3M5 1l3 3-3 3" fill="none" stroke="#0455a3" stroke-width="1.4"/></svg></a>
  </div>
</article>

<article class="abs post" style="top:733px">
  <div class="post-thumb" role="img" aria-label="Keys handed over in a room of moving boxes" style="background:linear-gradient(90deg,#b49a80,#d9c4ae)"></div>
  <div class="post-body">
    <h4 class="post-title">Lorem Ipsum is simply dummy text of the printing and typesetting industry.</h4>
    <div class="post-date"><svg width="9" height="9" viewBox="0 0 9 9"><rect x=".5" y="1.5" width="8" height="7" fill="none" stroke="#999"/><line x1=".5" y1="3.5" x2="8.5" y2="3.5" stroke="#999"/></svg>07 November 2016</div>
    <p class="post-text">Lorem Ipsum is simply dummy text of the printing and typesetting industry. Lorem Ipsum has been the industry's standard dummy text ever since the.</p>
    <a class="read-more" href="#">READ MORE <svg width="9" height="8" viewBox="0 0 9 8"><path d="M1 1l3 3-3 3M5 1l3 3-3 3" fill="none" stroke="#0455a3" stroke-width="1.4"/></svg></a>
  </div>
</article>

<nav class="abs pager">
  <a href="#" class="current">1</a><a href="#">2</a><a href="#">3</a><a href="#">...</a><a href="#">Next</a>
</nav>

<div class="abs footer-photo" role="img" aria-label="Faint background of a smiling person resting on a soft white rug"></div>
<svg class="abs footer-edge" width="747" height="76" viewBox="0 0 747 76">
  <polygon points="0,0 747,0 747,72 374,4 0,72" fill="#ffffff"/>
  <polyline points="0,72 374,4 747,72" fill="none" stroke="#0455a3" stroke-width="5"/>
</svg>

<div class="abs brand-foot">Bright Morrow Ltd</div>

<div class="abs foot-col links">
  <h3>USEFULL LINKS</h3>
  <ul>
    <li><i class="on"></i>Home</li>
    <li><i></i>About Us</li>
    <li><i></i>Services</li>
    <li><i></i>Blog</li>
    <li><i></i>Contact Us</li>
  </ul>
</div>

<div class="abs foot-col contact">
  <h3>GET IN TOUCH</h3>
  <div class="row" style="margin-top:10px"><svg width="13" height="12" viewBox="0 0 13 12"><path d="M1 2l3.5-1.2 4 1.2 3.5-1.2v9.2l-3.5 1.2-4-1.2L1 11.2z M4.5 .8v9.2 M8.5 2v9.2" fill="none" stroke="#0455a3"/></svg><span>101- Lorem ipsum is simple dummy text of print and type setting industry</span></div>
  <div class="row" style="margin-top:6px"><svg width="13" height="13" viewBox="0 0 13 13"><path d="M3 1l2 3-1.3 1.3a7 7 0 0 0 4 4L9 8l3 2-1.2 2C6 12 1 7 1 2.2z" fill="none" stroke="#0455a3"/></svg><span>0161 496 0732</span></div>
  <div class="row" style="margin-top:7px"><svg width="13" height="11" viewBox="0 0 13 11"><rect x=".5" y="1" width="12" height="9" fill="none" stroke="#0455a3"/><path d="M.5 1.5l6 4.5 6-4.5" fill="none" stroke="#0455a3"/></svg><span>info@brightmorrowltd.com</span></div>
</div>

<div class="abs foot-col news">
  <h3>NEWSLETTER</h3>
  <p>Would you like to receive exclusive access to articles, white papers and our regular monthly newsletter?</p>
  <span class="email">Enter Email Id</span>
  <span class="submit">SUBMIT</span>
</div>

<footer class="abs copyright">© 2016 <b>Bright Morrow -</b>&nbsp; All rights reserved.</footer>

</body>
</html>
```